Construction business card

I need a new business card, they can connect with my logo, brand.
What we do is residential house , design and build
I like: Navy blue / black
I attached our logo, brand,
and, some idea for business card.

```html
<!DOCTYPE html>
<html lang="en">
<head>
<meta charset="utf-8">
<title>Orvale Builders – Business Card</title>
<link rel="stylesheet" href="https://fonts.googleapis.com/css2?family=Varela+Round&family=Roboto:wght@400;700&display=swap">
<style>
  :root {
    --navy: #030a26;
    --blue: #3f86d0;
    --ink: #1b1b1b;
    --paper: #ffffff;
    --bg-top: #adc8cb;
    --bg-bottom: #dbfbfb;
  }
  * { margin: 0; padding: 0; box-sizing: border-box; }
  html, body { width: 1200px; height: 1200px; overflow: hidden; }
  body {
    background: linear-gradient(180deg, var(--bg-top) 0%, var(--bg-bottom) 100%);
    position: relative;
    font-family: "Roboto", Arial, sans-serif;
  }
  .card {
    position: absolute;
    left: 280px;
    width: 640px;
    height: 380px;
    box-shadow: 0 18px 40px rgba(20, 50, 60, 0.18);
    overflow: hidden;
  }
  .card--front { top: 170px; background: var(--paper); }
  .card--back { top: 650px; background: var(--navy); }

  .holder {
    position: absolute;
    left: 0; top: 78px;
    padding-left: 40px;
  }
  .holder__bar {
    position: absolute;
    left: 0; top: 4px;
    width: 14px; height: 52px;
    background: var(--blue);
    border-radius: 0 6px 6px 0;
  }
  .holder__name {
    font-family: "Varela Round", "Roboto", sans-serif;
    font-size: 40px;
    color: var(--blue);
    line-height: 1;
    letter-spacing: 0.5px;
  }
  .holder__role {
    font-size: 14px;
    color: var(--ink);
    margin-top: 2px;
  }

  .contact {
    position: absolute;
    left: 40px; top: 178px;
    list-style: none;
    font-size: 16px;
    color: var(--ink);
  }
  .contact__item {
    display: flex;
    align-items: flex-start;
    gap: 18px;
    margin-bottom: 9px;
    line-height: 1.35;
  }
  .contact__item--address { margin-bottom: 20px; }
  .contact__icon { width: 18px; height: 18px; flex: none; margin-top: 2px; }

  .brand {
    position: absolute;
    display: flex;
    align-items: center;
    gap: 12px;
    font-family: "Roboto", Arial, sans-serif;
    font-weight: 700;
    letter-spacing: 1px;
    text-transform: uppercase;
  }
  .brand__mark { width: 18px; height: 18px; flex: none; }
  .card--front .brand { right: 46px; top: 130px; font-size: 26px; color: var(--navy); }
  .card--front .brand__mark { background: var(--blue); }
  .card--back .brand { left: 80px; top: 120px; font-size: 34px; color: var(--paper); }
  .card--back .brand__mark { background: var(--blue); width: 22px; height: 22px; }
</style>
</head>
<body>

  <section class="card card--front" aria-label="Business card front">
    <div class="holder">
      <span class="holder__bar"></span>
      <h1 class="holder__name">Marcus Hale</h1>
      <p class="holder__role">Manager</p>
    </div>

    <ul class="contact">
      <li class="contact__item contact__item--address">
        <svg class="contact__icon" viewBox="0 0 20 20"><circle cx="10" cy="10" r="7.5" fill="none" stroke="#3f86d0" stroke-width="2.5"/><circle cx="10" cy="10" r="2.5" fill="#3f86d0"/></svg>
        <span>48 Fernhill Street,<br>Eastvale, Vic 3190</span>
      </li>
      <li class="contact__item">
        <svg class="contact__icon" viewBox="0 0 20 20"><path d="M4 2l3 0 1.5 4-2 1.5c1 2.2 2.8 4 5 5l1.5-2 4 1.5v3c0 1-1 2-2 2C8 17 3 12 2 4c0-1 1-2 2-2z" fill="#3f86d0"/></svg>
        <span>0400 555 218</span>
      </li>
      <li class="contact__item">
        <svg class="contact__icon" viewBox="0 0 20 20"><rect x="1.5" y="4" width="17" height="12" fill="#3f86d0"/><path d="M1.5 4l8.5 7 8.5-7" fill="none" stroke="#fff" stroke-width="1.5"/></svg>
        <span>info@orvalebuilders.com.au</span>
      </li>
      <li class="contact__item">
        <svg class="contact__icon" viewBox="0 0 20 20"><circle cx="10" cy="10" r="8" fill="#3f86d0"/><path d="M2 10h16M10 2v16M4 5.5h12M4 14.5h12" stroke="#fff" stroke-width="1"/><ellipse cx="10" cy="10" rx="3.5" ry="8" fill="none" stroke="#fff" stroke-width="1"/></svg>
        <span>www.orvalebuilders.com.au</span>
      </li>
    </ul>

    <div class="brand"><span class="brand__mark"></span>Orvale Builders</div>
  </section>

  <section class="card card--back" aria-label="Business card back">
    <div class="brand"><span class="brand__mark"></span>Orvale Builders</div>
  </section>

</body>
</html>
```